High-Converting Facebook Ads for Portals Drapes & Louvres (6 Products)

We are looking for a graphic designer to create high-quality Facebook & Instagram ads for our business: Portals Drapes and Louvres (Melbourne, Australia).

We require 6 separate ad designs, each for a different product:

Zipscreen Blinds

Outdoor Awnings

Plantation Shutters

Roller Shutters

Security Doors

Roller Blinds & Sheer Curtains

Ad Specifications:

Sizes:

1440 x 1800 px (4:5 ratio)

1080 x 1080 px (1:1 ratio)

1080 x 1920 px (9:16 ratio for Stories/Reels)

Format: PNG (high resolution, not blurry)

Designed specifically for Meta (Facebook/Instagram ads)

Mobile-friendly layout (clear, easy to read)

Style:

Bold, sales-driven, retail-style ads (NOT minimal)

Eye-catching and designed to generate leads

Clean, professional layout

Similar to promotional home improvement ads

Brand Colours:

Red: #E31E24

Blue: #0072BC

White backgrounds

Each ad must include:

“SALE NOW ON” banner at top

Our showroom address:
482 Upper Wattleby Road, Kestrel Heights (must be fully visible, not cut off)

Phone number: 9471 2658

Our logo (provided)

Badge: “Celebrating 13 YEARS in Business” (must be clean and readable)

Call to Action:

For 5 ads: “Book a FREE quote TODAY!”

For Security Doors ad: “ORDER NOW”

Offers / Pricing:

Most products: “UP TO 40% OFF”

Plantation Shutters: “FROM $299/sqm”

Security Doors: “FROM $750”

Content for each ad (examples):

Zipscreen Blinds:

Made to Measure

Fully Installed

Wind, Sun & Insect Protection

Outdoor Awnings:

Reduce Heat & Glare

Energy Saving

Custom Made

Plantation Shutters:

Modern & Elegant

Light & Privacy Control

Durable & Easy Care

Roller Shutters:

Security Protection

Block Heat & Noise

Total Light Control

Security Doors:

3 Point Locking

Premium Mesh

Custom Made

Blinds & Sheers:

Huge Range of Fabrics

Modern Soft Finish

Perfect for Any Room

Important Notes:

All text must be sharp and easy to read (no blur)

Layout must be balanced and not overcrowded

Ensure no text is cut off (especially address and headings)

Badge text must be straight and professional (no distortion)

Use high-quality, relevant images (we will provide references)

Goal:
Create ads that look professional, trustworthy, and generate enquiries/bookings for in-home quotes.

We are open to creative ideas but want a strong, bold retail-style ad that converts.
I have uploaed chatgpt mocks

Target Market(s)

Homeowners in Melbourne, Australia (typically aged 30–65) looking to improve their homes with blinds, shutters, awnings and security doors. Mid to high income households focused on quality, security, and modern home upgrades.

Industry/Entity Type

Home Improvement / Construction / Retail

Font styles to use
Sans Serif

Requirements
Must have
• Clear, bold and easy-to-read text (must be readable on mobile) High-quality, non-blurry design Strong “SALE” style layout (retail promotional look) Proper spacing (no overcrowded designs) All key info visible (address must NOT be cut off) Correct pricing and offers included Clean “13 YEARS” badge (no distortion or curved text) Consistent branding across all 6 ads
Nice to have
• Modern, slightly premium feel while still being bold Good use of contrast (red/blue/white) Subtle shadows or layering to improve depth Clean use of icons or bullet points Strong hierarchy (headline → benefits → offer → CTA) Variations in layout for testing different ad styles
Should not have
• Minimal or plain designs (we want bold, sales-driven ads) Hard-to-read fonts or script fonts Low-quality or blurry images Overcrowded layouts with too much text Important text cut off (especially address or headings) Overuse of effects or “cheap” looking graphics Yellow-heavy colour schemes (must follow brand colours)

```html
<!DOCTYPE html>
<html lang="en">
<head>
<meta charset="utf-8">
<title>Portals Drapes &amp; Louvres – Sale Ad Set</title>
<link rel="stylesheet" href="https://fonts.googleapis.com/css2?family=Poppins:wght@400;500;600;700;800;900&family=Oswald:wght@500;700&display=swap">
<style>
:root{
  --red:#E31E24;
  --blue:#0072BC;
  --navy:#0a4f86;
  --gold:#FFD21F;
  --ink:#1f1f1f;
  --page:#8f8f8f;
  --white:#ffffff;
  --sky-top:#eaf4fc;
  --sky-bottom:#cfe3f3;
}
*{box-sizing:border-box}
html,body{margin:0;padding:0}
body{width:1200px;height:3000px;overflow:hidden;background:var(--page);position:relative;font-family:"Poppins",sans-serif;color:var(--ink)}

.size-label{position:absolute;left:0;width:100%;margin:0;text-align:center;font-family:"Poppins",sans-serif;font-weight:700;font-size:52px;line-height:1;color:#2a2a2a;letter-spacing:-.5px}

.ad{position:absolute;overflow:hidden;background:var(--white);box-shadow:0 4px 14px rgba(0,0,0,.25)}
.ad>*{position:absolute}
.ad--sky{background:linear-gradient(180deg,var(--sky-top),var(--sky-bottom))}

.photo{left:0;width:100%}
.photo--zip{background:linear-gradient(160deg,#c9d3dc 0%,#9aa5ae 45%,#6f7983 100%)}
.photo--door{background:linear-gradient(90deg,#d9dde0 0%,#5f666b 30%,#b9bec2 55%,#e9ebec 100%)}
.photo--shutter{background:linear-gradient(180deg,#b7c3cc 0%,#8f969b 35%,#c49a72 70%,#9b7a5c 100%)}
.photo--bedroom{background:linear-gradient(180deg,#eef0f1 0%,#c8c9c9 45%,#6e6a66 100%)}
.photo--awning{background:linear-gradient(180deg,#c8b9a2 0%,#8d9a87 40%,#b2b6b8 75%,#8b8f92 100%)}
.photo--lounge{background:linear-gradient(180deg,#e9ecef 0%,#c3c2bd 45%,#8a7358 100%)}

.logo{display:flex;align-items:center;gap:.4em;white-space:nowrap}
.logo--center{left:0;width:100%;justify-content:center}
.logo-mark{display:block;width:1.05em;height:1.05em;background:var(--red)}
.logo-name{color:var(--blue);font-weight:700;letter-spacing:-.01em}

.headline{line-height:1}
.headline--center{left:0;width:100%;text-align:center}
.sale{display:block;color:var(--red);font-weight:900;line-height:.88;letter-spacing:-.01em}
.now{display:block;color:var(--blue);font-weight:800;line-height:1}
.offer{color:var(--ink);font-weight:500;white-space:nowrap;line-height:1}
.offer b{font-weight:800}
.offer sup{font-size:.55em;vertical-align:.7em}
.offer-bar{background:var(--red);color:var(--white);font-weight:600;display:flex;align-items:center;justify-content:center;white-space:nowrap}
.offer-bar--blue{background:var(--blue)}

.pill{background:var(--blue);color:var(--white);font-weight:700;border-radius:5px;padding:.22em .6em;white-space:nowrap;line-height:1.15}
.heading-light{color:var(--white);font-weight:700;white-space:nowrap}

.perks{list-style:none;margin:0;padding:0;color:var(--ink);font-weight:500;line-height:1.2}
.perks li{position:relative;padding-left:1.05em;margin-bottom:.45em}
.perks li::before{content:"";position:absolute;left:.1em;top:.35em;width:.48em;height:.48em;border-radius:50%;background:var(--red)}
.perks--light{color:var(--white)}
.perks--cols{display:grid;grid-template-columns:1fr 1fr;column-gap:.6em}

.cta{display:flex;flex-direction:column;justify-content:center;padding-left:.55em;color:var(--white);background:var(--red);border-radius:4px;line-height:1;box-shadow:0 3px 6px rgba(0,0,0,.2)}
.cta--blue{background:var(--blue)}
.cta--plain{background:none;box-shadow:none;color:var(--ink);padding-left:0}
.cta--plain .cta-free{color:var(--red)}
.cta-a{font-weight:400}
.cta-free{font-family:"Oswald",sans-serif;font-weight:700;font-size:2.7em;line-height:.95}
.cta-b{font-weight:700}

.order{background:var(--red);color:var(--white);display:flex;align-items:center;justify-content:center;text-align:center;font-family:"Oswald",sans-serif;font-weight:700;line-height:.9;border-radius:3px;box-shadow:0 3px 6px rgba(0,0,0,.2)}

.badge{border-radius:50%;background:var(--red);color:var(--white);display:flex;flex-direction:column;align-items:center;justify-content:center;text-align:center;font-family:"Oswald",sans-serif;font-weight:500;line-height:1.05;box-shadow:inset 0 0 0 .3em var(--red),inset 0 0 0 .42em rgba(255,255,255,.75),0 3px 8px rgba(0,0,0,.35)}
.badge b{color:var(--gold);font-weight:700;font-size:1.7em;line-height:1}
.badge span{font-size:.8em}

.stripe{left:0;width:100%}

.footer{left:0;width:100%;background:var(--blue);color:var(--white);display:flex;align-items:center;padding:0 .9em;gap:.7em}
.footer--light{background:var(--white);color:var(--ink);border-top:1px dashed #b9b9b9}
.f-phone{display:flex;align-items:center;gap:.3em;font-weight:700;white-space:nowrap}
.f-addr{display:flex;align-items:center;gap:.35em;font-size:.55em;line-height:1.2;padding-left:.8em;border-left:1px solid rgba(255,255,255,.6);white-space:nowrap}
.footer--light .f-addr{border-left-color:#bbb}
.f-addr small{display:block;font-size:.85em;font-weight:600;color:#ffd5d6}
.footer--light .f-addr small{color:var(--red)}
.ic{width:1.1em;height:1.1em;flex:none}
.f-addr .ic{width:1.6em;height:1.6em}

.contact{color:var(--white);font-size:9px;line-height:1.25}
.contact .f-phone{font-size:14px;margin-bottom:2px}
.contact small{display:block;font-weight:600;color:#ffd5d6}
.contact--dark{color:var(--ink)}
.contact--dark small{color:var(--red)}
</style>
</head>
<body>

<svg width="0" height="0" style="position:absolute" aria-hidden="true">
  <symbol id="i-phone" viewBox="0 0 24 24"><circle cx="12" cy="12" r="12" fill="#E31E24"/><path d="M8.2 6.5c.4-.3 1-.3 1.3.1l1.3 1.8c.3.4.2 1-.1 1.3l-.8.7c.6 1.3 1.6 2.4 2.9 3l.7-.8c.3-.4.9-.4 1.3-.1l1.8 1.3c.4.3.5.9.1 1.3l-1 1.1c-.5.5-1.3.7-2 .4-3-1.2-5.3-3.5-6.5-6.5-.3-.7-.1-1.5.4-2z" fill="#fff"/></symbol>
  <symbol id="i-pin" viewBox="0 0 24 24"><path d="M12 1C7.6 1 4 4.4 4 8.8 4 14.6 12 23 12 23s8-8.4 8-14.2C20 4.4 16.4 1 12 1z" fill="#E31E24"/><circle cx="12" cy="9" r="3" fill="#fff"/></symbol>
</svg>

<!-- ============ 4:5 SET ============ -->
<h2 class="size-label" style="top:91px">1440 x 1800 px</h2>

<!-- Zipscreen -->
<section class="ad ad--sky" style="left:63px;top:190px;width:335px;height:419px">
  <div class="photo photo--zip" role="img" aria-label="Home patio with outdoor zipscreen blinds" style="top:150px;height:225px"></div>
  <div class="logo logo--center" style="top:18px;font-size:12px"><i class="logo-mark"></i><span class="logo-name">Portals Drapes &amp; Louvres</span></div>
  <div class="headline" style="left:24px;top:70px"><span class="sale" style="font-size:46px">SALE</span><span class="now" style="font-size:31px">NOW ON</span></div>
  <div class="offer-bar" style="left:24px;top:146px;width:134px;height:22px;font-size:12.5px">UP TO 40% OFF</div>
  <div class="badge" style="left:50px;top:178px;width:92px;height:92px;font-size:12px"><span>CELEBRATING</span><b>13 YEARS</b><span>IN BUSINESS</span></div>
  <div class="pill" style="left:174px;top:74px;font-size:13px">Zipscreen Blinds</div>
  <ul class="perks" style="left:176px;top:102px;width:150px;font-size:10px"><li>Made to Measure</li><li>Fully Installed</li><li>Wind, Sun &amp; Insect Protection</li></ul>
  <div class="cta cta--blue" style="left:176px;top:180px;width:148px;height:78px;font-size:11px"><span class="cta-a">Book a</span><span class="cta-free">FREE</span><span class="cta-b">quote TODAY!</span></div>
  <div class="footer" style="top:369px;height:50px;font-size:15px"><span class="f-phone"><svg class="ic"><use href="#i-phone"/></svg>9471 2658</span><span class="f-addr"><svg class="ic"><use href="#i-pin"/></svg><span><small>Our showroom address</small>482 Upper Wattleby Road,<br>Kestrel Heights</span></span></div>
</section>

<!-- Security Doors -->
<section class="ad" style="left:432px;top:190px;width:335px;height:419px">
  <div class="logo" style="left:18px;top:66px;font-size:10.5px"><i class="logo-mark"></i><span class="logo-name">Portals Drapes &amp; Louvres</span></div>
  <div class="headline" style="left:160px;top:10px"><span class="sale" style="font-size:52px">SALE</span><span class="now" style="font-size:35px">NOW ON</span></div>
  <div class="offer" style="left:246px;top:96px;font-size:18px">FROM<br><b style="font-size:22px"><sup>$</sup>750</b></div>
  <div class="order" style="left:17px;top:100px;width:92px;height:70px;font-size:27px">ORDER<br>NOW</div>
  <div class="pill" style="left:114px;top:98px;font-size:12.5px">Security Doors</div>
  <ul class="perks" style="left:116px;top:124px;width:120px;font-size:9.5px"><li>3 Point Locking</li><li>Premium Mesh</li><li>Custom Made</li></ul>
  <div class="photo photo--door" role="img" aria-label="Front entry with security screen doors" style="top:182px;height:180px"></div>
  <div class="badge" style="left:196px;top:150px;width:82px;height:82px;font-size:11px"><span>CELEBRATING</span><b>13 YEARS</b><span>IN BUSINESS</span></div>
  <div class="footer" style="top:362px;height:57px;font-size:16px"><span class="f-phone"><svg class="ic"><use href="#i-phone"/></svg>9471 2658</span><span class="f-addr"><svg class="ic"><use href="#i-pin"/></svg><span><small>Our showroom address</small>482 Upper Wattleby Road,<br>Kestrel Heights</span></span></div>
</section>

<!-- Roller Shutters -->
<section class="ad" style="left:817px;top:190px;width:335px;height:419px">
  <div class="logo" style="left:18px;top:66px;font-size:10.5px"><i class="logo-mark"></i><span class="logo-name">Portals Drapes &amp; Louvres</span></div>
  <div class="headline" style="left:158px;top:10px"><span class="sale" style="font-size:52px">SALE</span><span class="now" style="font-size:35px">NOW ON</span></div>
  <div class="offer" style="left:158px;top:88px;font-size:18px">UP TO <b>40% OFF</b></div>
  <div class="photo photo--shutter" role="img" aria-label="House front with closed roller shutters" style="top:112px;height:175px"></div>
  <div class="badge" style="left:186px;top:100px;width:82px;height:82px;font-size:11px"><span>CELEBRATING</span><b>13 YEARS</b><span>IN BUSINESS</span></div>
  <div class="stripe" style="top:282px;height:137px;background:var(--blue)"></div>
  <div class="cta" style="left:22px;top:250px;width:112px;height:102px;font-size:13px"><span class="cta-a">Book a</span><span class="cta-free" style="font-size:3.1em">FREE</span><span class="cta-b">quote TODAY!</span></div>
  <div class="heading-light" style="left:152px;top:292px;font-size:16px">Roller Shutters</div>
  <ul class="perks perks--light perks--cols" style="left:152px;top:316px;width:170px;font-size:9.5px"><li>Security Protection</li><li>Block Heat &amp; Noise</li><li style="grid-column:1/3">Total Light Control</li></ul>
  <div class="footer" style="top:362px;height:57px;font-size:14px;border-top:1px solid rgba(255,255,255,.35)"><span class="f-phone"><svg class="ic"><use href="#i-phone"/></svg>9471 2658</span><span class="f-addr"><svg class="ic"><use href="#i-pin"/></svg><span><small>Our showroom address</small>482 Upper Wattleby Road,<br>Kestrel Heights</span></span></div>
</section>

<!-- Plantation Shutters -->
<section class="ad" style="left:63px;top:642px;width:335px;height:419px">
  <div class="logo" style="left:18px;top:66px;font-size:10.5px"><i class="logo-mark"></i><span class="logo-name">Portals Drapes &amp; Louvres</span></div>
  <div class="headline" style="left:155px;top:10px"><span class="sale" style="font-size:50px">SALE</span><span class="now" style="font-size:34px">NOW ON</span></div>
  <div class="offer" style="left:155px;top:86px;font-size:18px">FROM <b><sup>$</sup>299</b>/sqm</div>
  <div class="pill" style="left:155px;top:115px;font-size:12.5px">Plantation Shutters</div>
  <ul class="perks" style="left:157px;top:141px;width:170px;font-size:10px"><li>Modern &amp; Elegant</li><li>Light &amp; Privacy Control</li><li>Durable &amp; Easy Care</li></ul>
  <div class="cta" style="left:20px;top:92px;width:118px;height:100px;font-size:13px"><span class="cta-a">Book a</span><span class="cta-free" style="font-size:3.1em">FREE</span><span class="cta-b">quote TODAY!</span></div>
  <div class="photo photo--bedroom" role="img" aria-label="Bedroom with white plantation shutters" style="top:214px;height:205px"></div>
  <svg class="stripe" style="top:196px;height:40px" viewBox="0 0 335 40" preserveAspectRatio="none" aria-hidden="true"><polygon points="0,28 335,0 335,12 0,40" fill="#0072BC"/><polygon points="0,0 335,0 0,28" fill="#fff"/></svg>
  <div class="badge" style="left:122px;top:196px;width:78px;height:78px;font-size:10.5px"><span>CELEBRATING</span><b>13 YEARS</b><span>IN BUSINESS</span></div>
  <div class="contact" style="left:190px;top:348px"><span class="f-phone"><svg class="ic"><use href="#i-phone"/></svg>9471 2658</span><small>Our showroom address</small>482 Upper Wattleby Road,<br>Kestrel Heights</div>
</section>

<!-- Outdoor Awnings -->
<section class="ad" style="left:432px;top:642px;width:335px;height:419px">
  <div class="logo" style="left:18px;top:66px;font-size:10.5px"><i class="logo-mark"></i><span class="logo-name">Portals Drapes &amp; Louvres</span></div>
  <div class="headline" style="left:158px;top:10px"><span class="sale" style="font-size:50px">SALE</span><span class="now" style="font-size:34px">NOW ON</span></div>
  <div class="photo photo--awning" role="img" aria-label="Backyard patio under an outdoor awning" style="top:96px;height:176px"></div>
  <svg style="left:170px;top:96px;width:165px;height:176px" viewBox="0 0 165 176" preserveAspectRatio="none" aria-hidden="true"><polygon points="90,0 165,0 165,176 20,176" fill="#0072BC" opacity=".92"/></svg>
  <div class="badge" style="left:226px;top:100px;width:82px;height:82px;font-size:11px"><span>CELEBRATING</span><b>13 YEARS</b><span>IN BUSINESS</span></div>
  <div class="offer-bar offer-bar--blue" style="left:140px;top:246px;width:195px;height:26px;font-size:14px;font-weight:600">UP TO 40% OFF</div>
  <div class="cta cta--plain" style="left:22px;top:282px;width:140px;height:80px;font-size:17px"><span class="cta-a">Book a</span><span class="cta-free" style="font-size:2.9em">FREE</span><span class="cta-b">quote TODAY!</span></div>
  <div class="pill" style="left:172px;top:282px;font-size:12.5px">Outdoor Awnings</div>
  <ul class="perks" style="left:174px;top:308px;width:150px;font-size:10px"><li>Reduce Heat &amp; Glare</li><li>Energy Saving</li><li>Custom Made</li></ul>
  <div class="footer footer--light" style="top:366px;height:53px;font-size:16px;margin:0 14px;width:307px;padding:0 8px"><span class="f-phone"><svg class="ic"><use href="#i-phone"/></svg>9471 2658</span><span class="f-addr"><svg class="ic"><use href="#i-pin"/></svg><span><small>Our showroom address</small>482 Upper Wattleby Road,<br>Kestrel Heights</span></span></div>
</section>

<!-- Blinds & Sheers -->
<section class="ad ad--sky" style="left:817px;top:642px;width:335px;height:419px">
  <div class="logo logo--center" style="top:16px;font-size:12px"><i class="logo-mark"></i><span class="logo-name">Portals Drapes &amp; Louvres</span></div>
  <div class="headline" style="left:24px;top:68px"><span class="sale" style="font-size:44px">SALE</span><span class="now" style="font-size:30px">NOW ON</span></div>
  <div class="offer" style="left:24px;top:143px;font-size:15px">UP TO <b>40% OFF</b></div>
  <div class="pill" style="left:176px;top:68px;font-size:13px">Blinds &amp; Sheers</div>
  <ul class="perks" style="left:178px;top:96px;width:150px;font-size:10px"><li>Huge Range of Fabrics</li><li>Modern Soft Finish</li><li>Perfect for Any Room</li></ul>
  <div class="photo photo--lounge" role="img" aria-label="Living room with roller blinds and sheer curtains" style="top:210px;height:209px"></div>
  <div class="cta cta--blue" style="left:176px;top:184px;width:148px;height:70px;font-size:11px"><span class="cta-a">Book a</span><span class="cta-free">FREE</span><span class="cta-b">quote TODAY!</span></div>
  <div class="badge" style="left:48px;top:172px;width:86px;height:86px;font-size:11px"><span>CELEBRATING</span><b>13 YEARS</b><span>IN BUSINESS</span></div>
  <div class="footer" style="top:369px;height:50px;font-size:15px;background:rgba(0,82,150,.9)"><span class="f-phone"><svg class="ic"><use href="#i-phone"/></svg>9471 2658</span><span class="f-addr"><svg class="ic"><use href="#i-pin"/></svg><span><small>Our showroom address</small>482 Upper Wattleby Road,<br>Kestrel Heights</span></span></div>
</section>

<!-- ============ 1:1 SET ============ -->
<h2 class="size-label" style="top:1145px">1080 x 1080 px</h2>

<!-- Zipscreen -->
<section class="ad ad--sky" style="left:105px;top:1252px;width:251px;height:251px">
  <div class="photo photo--zip" role="img" aria-label="Home patio with outdoor zipscreen blinds" style="top:112px;height:139px"></div>
  <div class="logo logo--center" style="top:10px;font-size:9px"><i class="logo-mark"></i><span class="logo-name">Portals Drapes &amp; Louvres</span></div>
  <div class="headline" style="left:18px;top:46px"><span class="sale" style="font-size:34px">SALE</span><span class="now" style="font-size:22px">NOW ON</span></div>
  <div class="offer-bar" style="left:18px;top:98px;width:100px;height:16px;font-size:9.5px">UP TO 40% OFF</div>
  <div class="pill" style="left:132px;top:46px;font-size:9.5px">Zipscreen Blinds</div>
  <ul class="perks" style="left:134px;top:66px;width:112px;font-size:7.5px"><li>Made to Measure</li><li>Fully Installed</li><li>Wind, Sun &amp; Insect Protection</li></ul>
  <div style="left:132px;top:116px;width:119px;height:135px;background:var(--blue)"></div>
  <div class="cta cta--blue" style="left:132px;top:118px;width:119px;height:44px;font-size:8px;box-shadow:none"><span class="cta-a">Book a</span><span class="cta-free" style="font-size:2.4em">FREE</span><span class="cta-b">quote TODAY!</span></div>
  <div class="contact" style="left:140px;top:170px;font-size:7px"><span class="f-phone" style="font-size:10px"><svg class="ic"><use href="#i-phone"/></svg>9471 2658</span><small>Our showroom address</small>482 Upper Wattleby Road,<br>Kestrel Heights</div>
  <div class="badge" style="left:82px;top:108px;width:56px;height:56px;font-size:6.5px"><span>CELEBRATING</span><b>13 YEARS</b><span>IN BUSINESS</span></div>
</section>

<!-- Security Doors -->
<section class="ad" style="left:474px;top:1252px;width:251px;height:251px">
  <div class="logo" style="left:12px;top:38px;font-size:7.5px"><i class="logo-mark"></i><span class="logo-name">Portals Drapes &amp; Louvres</span></div>
  <div class="headline" style="left:122px;top:8px"><span class="sale" style="font-size:36px">SALE</span><span class="now" style="font-size:24px">NOW ON</span></div>
  <div class="offer" style="left:122px;top:64px;font-size:15px">FROM <b><sup>$</sup>750</b></div>
  <div class="photo photo--door" role="img" aria-label="Front entry with security screen doors" style="top:88px;height:122px;width:126px"></div>
  <div class="badge" style="left:22px;top:60px;width:56px;height:56px;font-size:6.5px"><span>CELEBRATING</span><b>13 YEARS</b><span>IN BUSINESS</span></div>
  <div class="pill" style="left:130px;top:88px;font-size:9px">Security Doors</div>
  <ul class="perks" style="left:132px;top:106px;width:112px;font-size:7px"><li>Security Protection</li><li>Block Heat &amp; Noise</li><li>Total Light Control</li></ul>
  <div class="order" style="left:134px;top:150px;width:82px;height:52px;font-size:20px">ORDER<br>NOW</div>
  <div class="footer" style="top:210px;height:41px;font-size:12px;padding:0 .8em"><span class="f-phone"><svg class="ic"><use href="#i-phone"/></svg>9471 2658</span><span class="f-addr"><svg class="ic"><use href="#i-pin"/></svg><span><small>Our showroom address</small>482 Upper Wattleby Road,<br>Kestrel Heights</span></span></div>
</section>

<!-- Roller Shutters -->
<section class="ad" style="left:859px;top:1252px;width:251px;height:251px">
  <div class="logo" style="left:12px;top:38px;font-size:7.5px"><i class="logo-mark"></i><span class="logo-name">Portals Drapes &amp; Louvres</span></div>
  <div class="headline" style="left:122px;top:8px"><span class="sale" style="font-size:36px">SALE</span><span class="now" style="font-size:24px">NOW ON</span></div>
  <div class="offer" style="left:122px;top:64px;font-size:12px">UP TO <b>40% OFF</b></div>
  <div class="photo photo--shutter" role="img" aria-label="House front with closed roller shutters" style="top:120px;height:92px"></div>
  <div class="stripe" style="top:80px;height:42px;background:var(--blue)"></div>
  <div class="cta" style="left:20px;top:56px;width:72px;height:62px;font-size:8.5px"><span class="cta-a">Book a</span><span class="cta-free" style="font-size:3em">FREE</span><span class="cta-b">quote TODAY!</span></div>
  <div class="heading-light" style="left:104px;top:82px;font-size:10px">Roller Shutters</div>
  <ul class="perks perks--light perks--cols" style="left:104px;top:96px;width:140px;font-size:6.5px"><li>Security Protection</li><li>Total Light Control</li><li>Block Heat &amp; Noise</li></ul>
  <div class="badge" style="left:180px;top:140px;width:56px;height:56px;font-size:6.5px"><span>CELEBRATING</span><b>13 YEARS</b><span>IN BUSINESS</span></div>
  <div class="footer" style="top:212px;height:39px;font-size:11px;padding:0 .8em"><span class="f-phone"><svg class="ic"><use href="#i-phone"/></svg>9471 2658</span><span class="f-addr"><svg class="ic"><use href="#i-pin"/></svg><span><small>Our showroom address</small>482 Upper Wattleby Road, Kestrel Heights</span></span></div>
</section>

<!-- Plantation Shutters -->
<section class="ad" style="left:105px;top:1532px;width:251px;height:251px">
  <div class="logo" style="left:12px;top:38px;font-size:7.5px"><i class="logo-mark"></i><span class="logo-name">Portals Drapes &amp; Louvres</span></div>
  <div class="headline" style="left:118px;top:8px"><span class="sale" style="font-size:34px">SALE</span><span class="now" style="font-size:23px">NOW ON</span></div>
  <div class="offer" style="left:118px;top:60px;font-size:12px">FROM <b><sup>$</sup>299</b>/sqm</div>
  <div class="pill" style="left:118px;top:76px;font-size:8.5px">Plantation Shutters</div>
  <ul class="perks perks--cols" style="left:120px;top:94px;width:126px;font-size:6.5px"><li>Modern &amp; Elegant</li><li>Durable &amp; Easy Care</li><li>Light &amp; Privacy Control</li></ul>
  <div class="cta" style="left:18px;top:56px;width:80px;height:64px;font-size:9px"><span class="cta-a">Book a</span><span class="cta-free" style="font-size:2.9em">FREE</span><span class="cta-b">quote TODAY!</span></div>
  <div class="photo photo--bedroom" role="img" aria-label="Bedroom with white plantation shutters" style="top:128px;height:123px"></div>
  <div class="badge" style="left:86px;top:118px;width:56px;height:56px;font-size:6.5px"><span>CELEBRATING</span><b>13 YEARS</b><span>IN BUSINESS</span></div>
  <div class="contact" style="left:144px;top:200px;font-size:6.5px"><span class="f-phone" style="font-size:9.5px"><svg class="ic"><use href="#i-phone"/></svg>9471 2658</span><small>Our showroom address</small>482 Upper Wattleby Road,<br>Kestrel Heights</div>
</section>

<!-- Outdoor Awnings -->
<section class="ad" style="left:474px;top:1532px;width:251px;height:251px">
  <div class="logo" style="left:12px;top:38px;font-size:7.5px"><i class="logo-mark"></i><span class="logo-name">Portals Drapes &amp; Louvres</span></div>
  <div class="headline" style="left:122px;top:8px"><span class="sale" style="font-size:36px">SALE</span><span class="now" style="font-size:24px">NOW ON</span></div>
  <div class="photo photo--awning" role="img" aria-label="Backyard patio under an outdoor awning" style="top:62px;height:122px"></div>
  <svg style="left:120px;top:62px;width:131px;height:122px" viewBox="0 0 131 122" preserveAspectRatio="none" aria-hidden="true"><polygon points="80,0 131,0 131,122 20,122" fill="#0072BC" opacity=".92"/></svg>
  <div class="badge" style="left:170px;top:66px;width:56px;height:56px;font-size:6.5px"><span>CELEBRATING</span><b>13 YEARS</b><span>IN BUSINESS</span></div>
  <div class="offer-bar offer-bar--blue" style="left:106px;top:164px;width:145px;height:20px;font-size:10.5px">UP TO 40% OFF</div>
  <div class="cta cta--plain" style="left:14px;top:188px;width:95px;height:58px;font-size:11px"><span class="cta-a">Book a</span><span class="cta-free" style="font-size:2.7em">FREE</span><span class="cta-b">quote TODAY!</span></div>
  <div class="pill" style="left:112px;top:190px;font-size:8px">Outdoor Awnings</div>
  <ul class="perks perks--cols" style="left:112px;top:205px;width:134px;font-size:6px"><li>Reduce Heat &amp; Glare</li><li>Energy Saving</li><li style="grid-column:2">Custom Made</li></ul>
  <div class="contact contact--dark" style="left:112px;top:228px;font-size:5.8px"><b>Call us today! 9471 2658</b><br>482 Upper Wattleby Road, Kestrel Heights</div>
</section>

<!-- Blinds & Sheers -->
<section class="ad ad--sky" style="left:859px;top:1532px;width:251px;height:251px">
  <div class="logo logo--center" style="top:10px;font-size:9px"><i class="logo-mark"></i><span class="logo-name">Portals Drapes &amp; Louvres</span></div>
  <div class="headline" style="left:18px;top:46px"><span class="sale" style="font-size:33px">SALE</span><span class="now" style="font-size:22px">NOW ON</span></div>
  <div class="offer" style="left:18px;top:96px;font-size:11px">UP TO <b>40% OFF</b></div>
  <div class="pill" style="left:132px;top:46px;font-size:9.5px">Blinds &amp; Sheers</div>
  <ul class="perks" style="left:134px;top:66px;width:112px;font-size:7px"><li>Huge Range of Fabrics</li><li>Modern Soft Finish</li><li>Perfect for Any Room</li></ul>
  <div class="photo photo--lounge" role="img" aria-label="Living room with roller blinds and sheer curtains" style="top:112px;height:139px"></div>
  <div style="left:132px;top:116px;width:119px;height:135px;background:var(--blue)"></div>
  <div class="cta cta--blue" style="left:132px;top:118px;width:119px;height:44px;font-size:8px;box-shadow:none"><span class="cta-a">Book a</span><span class="cta-free" style="font-size:2.4em">FREE</span><span class="cta-b">quote TODAY!</span></div>
  <div class="contact" style="left:140px;top:170px;font-size:7px"><span class="f-phone" style="font-size:10px"><svg class="ic"><use href="#i-phone"/></svg>9471 2658</span><small>Our showroom address</small>482 Upper Wattleby Road,<br>Kestrel Heights</div>
  <div class="badge" style="left:30px;top:110px;width:56px;height:56px;font-size:6.5px"><span>CELEBRATING</span><b>13 YEARS</b><span>IN BUSINESS</span></div>
</section>

<!-- ============ 9:16 SET ============ -->
<h2 class="size-label" style="top:1881px">1080 x 1920 px</h2>

<!-- Zipscreen -->
<section class="ad ad--sky" style="left:105px;top:1972px;width:251px;height:449px">
  <div class="photo photo--zip" role="img" aria-label="Home patio with outdoor zipscreen blinds" style="top:160px;height:240px"></div>
  <div class="logo logo--center" style="top:14px;font-size:9.5px"><i class="logo-mark"></i><span class="logo-name">Portals Drapes &amp; Louvres</span></div>
  <div class="headline headline--center" style="top:52px"><span class="sale" style="font-size:46px">SALE</span><span class="now" style="font-size:30px">NOW ON</span></div>
  <div class="offer-bar" style="left:55px;top:128px;width:141px;height:22px;font-size:13px">UP TO 40% OFF</div>
  <div class="cta cta--blue" style="left:14px;top:160px;width:100px;height:80px;font-size:10.5px"><span class="cta-a">Book a</span><span class="cta-free" style="font-size:2.7em">FREE</span><span class="cta-b">quote TODAY!</span></div>
  <div class="pill" style="left:122px;top:160px;font-size:10px">Zipscreen Blinds</div>
  <ul class="perks" style="left:124px;top:182px;width:120px;font-size:7.5px"><li>Made to Measure</li><li>Fully Installed</li><li>Wind, Sun &amp; Insect Protection</li></ul>
  <div class="badge" style="left:144px;top:236px;width:66px;height:66px;font-size:7.5px"><span>CELEBRATING</span><b>13 YEARS</b><span>IN BUSINESS</span></div>
  <div class="footer" style="top:398px;height:51px;font-size:12px;padding:0 .8em"><span class="f-phone"><svg class="ic"><use href="#i-phone"/></svg>9471 2658</span><span class="f-addr"><svg class="ic"><use href="#i-pin"/></svg><span><small>Our showroom address</small>482 Upper Wattleby Road,<br>Kestrel Heights</span></span></div>
</section>

<!-- Security Doors -->
<section class="ad" style="left:474px;top:1972px;width:251px;height:449px">
  <div class="logo logo--center" style="top:14px;font-size:9.5px"><i class="logo-mark"></i><span class="logo-name">Portals Drapes &amp; Louvres</span></div>
  <div class="headline headline--center" style="top:52px"><span class="sale" style="font-size:46px">SALE</span><span class="now" style="font-size:30px">NOW ON</span></div>
  <div class="offer headline--center" style="top:130px;font-size:19px;text-align:center">FROM <b><sup>$</sup>750</b></div>
  <div class="order" style="left:26px;top:162px;width:74px;height:58px;font-size:22px">ORDER<br>NOW</div>
  <div class="pill" style="left:108px;top:162px;font-size:10px">Security Doors</div>
  <ul class="perks" style="left:110px;top:184px;width:130px;font-size:7.5px"><li>3 Point Locking</li><li>Premium Mesh</li><li>Custom Made</li></ul>
  <div class="photo photo--door" role="img" aria-label="Front entry with security screen doors" style="top:230px;height:170px"></div>
  <div class="badge" style="left:146px;top:210px;width:64px;height:64px;font-size:7.5px"><span>CELEBRATING</span><b>13 YEARS</b><span>IN BUSINESS</span></div>
  <div class="footer" style="top:398px;height:51px;font-size:12px;padding:0 .8em"><span class="f-phone"><svg class="ic"><use href="#i-phone"/></svg>9471 2658</span><span class="f-addr"><svg class="ic"><use href="#i-pin"/></svg><span><small>Our showroom address</small>482 Upper Wattleby Road,<br>Kestrel Heights</span></span></div>
</section>

<!-- Roller Shutters -->
<section class="ad" style="left:859px;top:1972px;width:251px;height:449px">
  <div class="logo logo--center" style="top:14px;font-size:9.5px"><i class="logo-mark"></i><span class="logo-name">Portals Drapes &amp; Louvres</span></div>
  <div class="headline headline--center" style="top:52px"><span class="sale" style="font-size:46px">SALE</span><span class="now" style="font-size:30px">NOW ON</span></div>
  <div class="offer headline--center" style="top:130px;font-size:17px;text-align:center">UP TO <b>40% OFF</b></div>
  <div class="cta" style="left:24px;top:160px;width:84px;height:78px;font-size:10px"><span class="cta-a">Book a</span><span class="cta-free" style="font-size:2.9em">FREE</span><span class="cta-b">quote TODAY!</span></div>
  <div class="pill" style="left:114px;top:160px;font-size:10px">Roller Shutters</div>
  <ul class="perks" style="left:116px;top:182px;width:130px;font-size:7.5px"><li>Security Protection</li><li>Block Heat &amp; Noise</li><li>Total Light Control</li></ul>
  <div class="photo photo--shutter" role="img" aria-label="House front with closed roller shutters" style="top:244px;height:156px"></div>
  <div class="badge" style="left:96px;top:222px;width:64px;height:64px;font-size:7.5px"><span>CELEBRATING</span><b>13 YEARS</b><span>IN BUSINESS</span></div>
  <div class="footer" style="top:398px;height:51px;font-size:12px;padding:0 .8em"><span class="f-phone"><svg class="ic"><use href="#i-phone"/></svg>9471 2658</span><span class="f-addr"><svg class="ic"><use href="#i-pin"/></svg><span><small>Our showroom address</small>482 Upper Wattleby Road,<br>Kestrel Heights</span></span></div>
</section>

<!-- Plantation Shutters -->
<section class="ad" style="left:105px;top:2446px;width:251px;height:449px">
  <div class="logo logo--center" style="top:14px;font-size:9.5px"><i class="logo-mark"></i><span class="logo-name">Portals Drapes &amp; Louvres</span></div>
  <div class="headline headline--center" style="top:52px"><span class="sale" style="font-size:46px">SALE</span><span class="now" style="font-size:30px">NOW ON</span></div>
  <div class="offer headline--center" style="top:130px;font-size:18px;text-align:center">FROM <b><sup>$</sup>299</b>/sqm</div>
  <div class="cta" style="left:12px;top:162px;width:88px;height:76px;font-size:10px"><span class="cta-a">Book a</span><span class="cta-free" style="font-size:2.9em">FREE</span><span class="cta-b">quote TODAY!</span></div>
  <div class="pill" style="left:106px;top:162px;font-size:9.5px">Plantation Shutters</div>
  <ul class="perks" style="left:108px;top:184px;width:136px;font-size:7.5px"><li>Modern &amp; Elegant</li><li>Light &amp; Privacy Control</li><li>Durable &amp; Easy Care</li></ul>
  <div class="photo photo--bedroom" role="img" aria-label="Bedroom with white plantation shutters" style="top:250px;height:150px"></div>
  <svg class="stripe" style="top:236px;height:30px" viewBox="0 0 251 30" preserveAspectRatio="none" aria-hidden="true"><polygon points="0,20 251,0 251,10 0,30" fill="#0072BC"/><polygon points="0,0 251,0 0,20" fill="#fff"/></svg>
  <div class="badge" style="left:74px;top:232px;width:64px;height:64px;font-size:7.5px"><span>CELEBRATING</span><b>13 YEARS</b><span>IN BUSINESS</span></div>
  <div class="footer" style="top:398px;height:51px;font-size:12px;padding:0 .8em"><span class="f-phone"><svg class="ic"><use href="#i-phone"/></svg>9471 2658</span><span class="f-addr"><svg class="ic"><use href="#i-pin"/></svg><span><small>Our showroom address</small>482 Upper Wattleby Road,<br>Kestrel Heights</span></span></div>
</section>

<!-- Outdoor Awnings -->
<section class="ad" style="left:474px;top:2446px;width:251px;height:449px">
  <div class="logo logo--center" style="top:14px;font-size:9.5px"><i class="logo-mark"></i><span class="logo-name">Portals Drapes &amp; Louvres</span></div>
  <div class="headline headline--center" style="top:52px"><span class="sale" style="font-size:46px">SALE</span><span class="now" style="font-size:30px">NOW ON</span></div>
  <div class="offer headline--center" style="top:130px;font-size:17px;text-align:center">UP TO <b>40% OFF</b></div>
  <div class="photo photo--awning" role="img" aria-label="Backyard patio under an outdoor awning" style="top:156px;height:130px"></div>
  <svg style="left:110px;top:156px;width:141px;height:130px" viewBox="0 0 141 130" preserveAspectRatio="none" aria-hidden="true"><polygon points="90,0 141,0 141,130 40,130" fill="#0072BC" opacity=".92"/></svg>
  <div class="badge" style="left:146px;top:168px;width:62px;height:62px;font-size:7.5px"><span>CELEBRATING</span><b>13 YEARS</b><span>IN BUSINESS</span></div>
  <div class="cta" style="left:14px;top:286px;width:96px;height:78px;font-size:10.5px"><span class="cta-a">Book a</span><span class="cta-free" style="font-size:2.9em">FREE</span><span class="cta-b">quote TODAY!</span></div>
  <div class="pill" style="left:116px;top:290px;font-size:10px">Outdoor Awnings</div>
  <ul class="perks" style="left:118px;top:312px;width:126px;font-size:7.5px"><li>Reduce Heat &amp; Glare</li><li>Energy Saving</li><li>Custom Made</li></ul>
  <div class="footer footer--light" style="top:398px;height:51px;font-size:12px;padding:0 .8em"><span class="f-phone"><svg class="ic"><use href="#i-phone"/></svg>9471 2658</span><span class="f-addr"><svg class="ic"><use href="#i-pin"/></svg><span><small>Our showroom address</small>482 Upper Wattleby Road,<br>Kestrel Heights</span></span></div>
</section>

<!-- Blinds & Sheers -->
<section class="ad" style="left:859px;top:2446px;width:251px;height:449px">
  <div class="logo logo--center" style="top:14px;font-size:9.5px"><i class="logo-mark"></i><span class="logo-name">Portals Drapes &amp; Louvres</span></div>
  <div class="headline headline--center" style="top:52px"><span class="sale" style="font-size:44px">SALE</span><span class="now" style="font-size:28px">NOW ON</span></div>
  <div class="offer headline--center" style="top:124px;font-size:18px;text-align:center">UP TO <b>40% OFF</b></div>
  <div class="cta cta--blue" style="left:22px;top:152px;width:88px;height:76px;font-size:10px"><span class="cta-a">Book a</span><span class="cta-free" style="font-size:3em">FREE</span><span class="cta-b">quote TODAY!</span></div>
  <div class="pill" style="left:116px;top:150px;font-size:10px">Blinds &amp; Sheers</div>
  <ul class="perks" style="left:118px;top:172px;width:126px;font-size:7.5px"><li>Huge Range of Fabrics</li><li>Modern Soft Finish</li><li>Perfect for Any Room</li></ul>
  <div class="photo photo--lounge" role="img" aria-label="Living room with roller blinds and sheer curtains" style="top:240px;height:160px"></div>
  <div class="badge" style="left:108px;top:222px;width:62px;height:62px;font-size:7.5px"><span>CELEBRATING</span><b>13 YEARS</b><span>IN BUSINESS</span></div>
  <div class="footer" style="top:398px;height:51px;font-size:12px;padding:0 .8em"><span class="f-phone"><svg class="ic"><use href="#i-phone"/></svg>9471 2658</span><span class="f-addr"><svg class="ic"><use href="#i-pin"/></svg><span><small>Our showroom address</small>482 Upper Wattleby Road,<br>Kestrel Heights</span></span></div>
</section>

</body>
</html>
```